Quorva - corporate Business Card

We need a good look and innovative business card for a new start up company based in Los Angeles called "Quorva". We are in a payment business, including payment card, app, and ewallet. We are expert in online payment and Card not present (CNP) transaction.
We need an innovative, modern business card.

Our logo font is Aero Matics

Target Market(s)

Startup - Bank - Online Payment - Card Manufacturing

Industry/Entity Type

Startup

Contact Information for Business Card

phone: 555 014 7396 - Address: 4172 Marlowe blvd, Cylver City, CA 90299

Requirements
Must have
• Message: innovative, professional, expert, high tech, trust, online payment expert, security
Nice to have
• no comment
Should not have
• no Comment

```html
<!DOCTYPE html>
<html lang="en">
<head>
<meta charset="UTF-8">
<title>Quorva – Business Card</title>
<link href="https://fonts.googleapis.com/css2?family=Lato:wght@400;700&display=swap" rel="stylesheet">
<style>
  :root {
    --backdrop: #2b2b2d;
    --card-dark: #212c33;
    --card-light: #ffffff;
    --brand-red: #c1202f;
    --ink: #2a2a2a;
    --rule: #3a3a3a;
    --muted-light: #e8ecef;
  }
  * { box-sizing: border-box; margin: 0; padding: 0; }
  html, body {
    width: 1200px; height: 1000px; overflow: hidden;
    background: var(--backdrop);
    font-family: "Lato", sans-serif;
  }
  .stage { position: relative; width: 1200px; height: 1000px; }

  .card { position: absolute; border-radius: 26px; }

  .card-back {
    left: 380px; top: 30px; width: 700px; height: 400px;
    background: var(--card-dark);
    box-shadow: 0 14px 30px rgba(0,0,0,.45);
  }
  .card-back .emblem {
    position: absolute; left: 50%; top: 120px; transform: translateX(-50%);
    width: 150px; height: 150px; border-radius: 50%;
    background: var(--brand-red);
  }
  .card-back .web {
    position: absolute; left: 0; right: 0; top: 330px;
    text-align: center; color: var(--muted-light);
    font-size: 18px; letter-spacing: 6px;
  }

  .card-front {
    left: 140px; top: 440px; width: 900px; height: 514px;
    background: var(--card-light);
    box-shadow: 0 16px 34px rgba(0,0,0,.5);
  }
  .brand { position: absolute; left: 70px; top: 60px; display: flex; align-items: center; gap: 14px; }
  .brand-dot { width: 80px; height: 80px; border-radius: 50%; background: var(--brand-red); }
  .brand-name { color: var(--brand-red); font-size: 58px; font-weight: 700; letter-spacing: 1px; }

  .person { position: absolute; left: 70px; top: 200px; }
  .person-name { color: var(--brand-red); font-size: 34px; font-weight: 700; line-height: 1.1; }
  .person-role { color: var(--ink); font-size: 24px; margin-top: 2px; }

  .divider { position: absolute; left: 66px; right: 60px; top: 292px; height: 2px; background: var(--rule); }

  .contacts { position: absolute; left: 70px; top: 316px; list-style: none; }
  .contacts li { display: flex; align-items: center; gap: 18px; color: var(--ink); font-size: 22px; height: 38px; }
  .contacts svg { width: 20px; height: 20px; fill: var(--brand-red); flex: none; }
  .contacts .accent { color: var(--brand-red); }

  .address { position: absolute; right: 60px; bottom: 36px; color: var(--ink); font-size: 22px; line-height: 1.35; text-align: left; }
</style>
</head>
<body>
<main class="stage">
  <section class="card card-back" aria-label="Card back">
    <div class="emblem"></div>
    <p class="web">www.quorvapay.com</p>
  </section>

  <section class="card card-front" aria-label="Card front">
    <div class="brand">
      <span class="brand-dot"></span>
      <span class="brand-name">quorva</span>
    </div>

    <div class="person">
      <p class="person-name">Daniel Reyes</p>
      <p class="person-role">Ceo &amp; Founder</p>
    </div>

    <div class="divider"></div>

    <ul class="contacts">
      <li>
        <svg viewBox="0 0 24 24" aria-hidden="true"><path d="M6.6 10.8a15.2 15.2 0 0 0 6.6 6.6l2.2-2.2a1 1 0 0 1 1-.25 11.4 11.4 0 0 0 3.6.57 1 1 0 0 1 1 1V20a1 1 0 0 1-1 1A17 17 0 0 1 3 4a1 1 0 0 1 1-1h3.5a1 1 0 0 1 1 1c0 1.25.2 2.45.57 3.57a1 1 0 0 1-.25 1z"/></svg>
        555 014 7396
      </li>
      <li>
        <svg viewBox="0 0 24 24" aria-hidden="true"><path d="M2 5h20L12 12.5z"/><path d="M2 7l10 7.5L22 7v12H2z"/></svg>
        daniel@quorvapay.com
      </li>
      <li>
        <svg viewBox="0 0 24 24" aria-hidden="true"><circle cx="12" cy="12" r="10"/><path d="M2 12h20M12 2c3 3 3 17 0 20M12 2c-3 3-3 17 0 20M4 7h16M4 17h16" stroke="#fff" stroke-width="1.2" fill="none"/></svg>
        <span>www.<span class="accent">quorvapay</span>.com</span>
      </li>
    </ul>

    <p class="address">4172 Marlowe blvd<br>Fenmore Bay, CA 90299</p>
  </section>
</main>
</body>
</html>
```